A compelling brochure for a children's charity to encourage donations

We are looking for a 4-page A-4 booklet (1 x A3 page folded in half). the Bright Path Foundation is a non-profit organisation that aims to reduce the incidence and impact of children's critical injury in Australia. The brochure will give people who are new to the charity, an overview of who we are, what we do, why we do it and how they can help. You can reference our website www.brightpathfund.org.au for colours and styles. The final design should encourage people to make a donation by being positive and powerful.
Use the text in the uploaded files.

```html
<!DOCTYPE html>
<html lang="en">
<head>
<meta charset="utf-8">
<title>Bright Path Foundation – Brochure Cover</title>
<link rel="stylesheet" href="https://fonts.googleapis.com/css2?family=Noto+Serif:wght@400&display=swap">
<style>
  :root {
    --sky-top: #3d9be6;
    --sky-low: #8fc7f0;
    --foliage: #4f8a2e;
    --jersey: #f07a1c;
    --magenta: #b3138f;
    --magenta-deep: #950a78;
    --frame: #c63aa8;
    --paper: #ffffff;
    --brand: #b3138f;
    --accent: #e8941e;
  }
  html, body {
    margin: 0;
    padding: 0;
    width: 848px;
    height: 1200px;
    overflow: hidden;
    background: var(--paper);
  }
  .cover {
    position: relative;
    width: 848px;
    height: 1200px;
    overflow: hidden;
    font-family: "Noto Serif", Georgia, serif;
  }
  .cover__photo {
    position: absolute;
    left: 0; top: 0;
    width: 848px; height: 690px;
    background:
      linear-gradient(180deg, transparent 0%, transparent 45%, rgba(240,122,28,0.55) 62%, rgba(200,200,200,0.5) 100%),
      linear-gradient(90deg, var(--foliage) 0%, var(--sky-low) 22%, var(--sky-top) 50%, var(--sky-low) 78%, var(--foliage) 100%);
  }
  .cover__band {
    position: absolute;
    left: 0; top: 690px;
    width: 848px; height: 400px;
    background: var(--magenta);
  }
  .cover__footer {
    position: absolute;
    left: 0; top: 1090px;
    width: 848px; height: 110px;
    background: var(--magenta-deep);
  }
  .cover__headline {
    position: absolute;
    left: 52px; top: 700px;
    margin: 0;
    color: var(--paper);
    font-weight: 400;
    font-size: 37px;
    line-height: 57px;
    letter-spacing: 0.2px;
  }
  .brand-card {
    position: absolute;
    left: 410px; top: 918px;
    width: 382px; height: 222px;
    background: var(--frame);
  }
  .brand-card__inner {
    position: absolute;
    left: 14px; top: 14px;
    width: 354px; height: 203px;
    background: var(--paper);
  }
  .brand-card__name {
    position: absolute;
    left: 0; right: 0; top: 46px;
    text-align: center;
    color: var(--brand);
    font-size: 46px;
    line-height: 56px;
  }
  .brand-card__rule {
    position: absolute;
    left: 14px; right: 14px; top: 152px;
    height: 2px;
    background: var(--accent);
  }
  .brand-card__url {
    position: absolute;
    left: 0; right: 0; top: 160px;
    text-align: center;
    color: var(--accent);
    font-size: 21px;
  }
</style>
</head>
<body>
  <main class="cover">
    <div class="cover__photo" role="img" aria-label="Photo of a smiling family riding bicycles in helmets and sunglasses under a blue summer sky"></div>
    <div class="cover__band"></div>
    <div class="cover__footer"></div>
    <h1 class="cover__headline">Reducing the incidence<br>and impact of children’s critical<br>injury in Australia.</h1>
    <div class="brand-card">
      <div class="brand-card__inner">
        <div class="brand-card__name">Bright Path</div>
        <div class="brand-card__rule"></div>
        <div class="brand-card__url">www.brightpathfund.org.au</div>
      </div>
    </div>
  </main>
</body>
</html>
```